Natural healthcare clinic needs stationery and business card design

We have had a logo developed by Pixel Harbor and are now looking at utilising it for a new business concept. The concept is a natural healthcare clinic that hosts a number of small businesses. The individual practitioners may want to utilise the host business stationery to provide a consistent message to clients.

I am looking for a stationery design - letterhead, DL brochure template and business card that uses our logo. The business name 'Bright Meadows' is all about getting rhythm back into your life so you can be fit and healthy. The stationery design should reflect this.

There are a couple of requirements for the business card, it needs to be double-sided with black and white back. There should be lines to write appointment times on. The cards may need to be custom named on the front for example Carol Fenwick, Remedial Therapist and Aromatherapist. Therefore if a template can be provided so we can customise this information using MS Publisher, it would be appreciated.

The DL brochure template needs to be A4 folded to DL. I am looking for a consistent brand message that can be utilised to produce our own clinic brochures.

The natural healthcare clinic will host the following types of businesses - remedial massage, pregnancy massage, oncology massage, aromatherapy, acupuncture - as a bit of a guide.

Target Market(s)

25-45 year old male and females who work full time.

Industry/Entity Type

Healthcare

Requirements
Must have
• Use the logo I have already.

```html
<!DOCTYPE html>
<html lang="en">
<head>
<meta charset="utf-8">
<title>Bright Meadows – Business Card</title>
<link rel="stylesheet" href="https://fonts.googleapis.com/css2?family=Open+Sans:wght@400;600&display=swap">
<style>
  :root {
    --backdrop: #e9e4da;
    --card-white: #ffffff;
    --card-black: #0b0b0b;
    --leaf-green: #8ab32a;
    --deep-green: #5c8a12;
    --olive-text: #6b7d2e;
    --peach: #f6c29c;
    --ink: #4a4a40;
    --accent-orange: #e8802a;
    --white: #ffffff;
  }
  * { box-sizing: border-box; margin: 0; padding: 0; }
  html, body { width: 1200px; height: 1024px; overflow: hidden; }
  body {
    background: var(--backdrop);
    font-family: "Open Sans", Arial, sans-serif;
    position: relative;
  }
  .card {
    position: absolute;
    left: 250px;
    width: 700px;
    height: 400px;
    border-radius: 26px;
    overflow: hidden;
    box-shadow: 0 10px 28px rgba(0,0,0,0.18);
  }
  .card-front { top: 72px; background: var(--card-white); }
  .card-back { top: 552px; background: var(--card-black); }

  .front-swoosh { position: absolute; inset: 0; }

  .brand-mark {
    position: absolute;
    display: flex;
    align-items: center;
    gap: 12px;
  }
  .brand-dot {
    width: 28px; height: 28px;
    border-radius: 50%;
    background: var(--leaf-green);
    flex: none;
  }
  .brand-name {
    font-weight: 400;
    font-size: 34px;
    color: var(--olive-text);
    letter-spacing: -0.5px;
    white-space: nowrap;
  }
  .card-front .brand-mark { left: 40px; top: 222px; }

  .contact-block {
    position: absolute;
    left: 310px;
    top: 40px;
    color: var(--ink);
  }
  .contact-name {
    font-size: 19px;
    font-weight: 600;
    color: var(--olive-text);
    margin-bottom: 14px;
  }
  .contact-name .job-title { font-weight: 400; color: var(--ink); }
  .contact-address { font-size: 14px; line-height: 1.35; margin-bottom: 10px; }
  .contact-line {
    display: flex; align-items: center; gap: 8px;
    font-size: 14px; line-height: 1.55;
  }
  .contact-line svg { width: 13px; height: 13px; flex: none; }

  .divider-line {
    position: absolute;
    left: 340px; top: 238px;
    width: 140px; height: 3px;
    background: linear-gradient(90deg, rgba(92,138,18,0) 0%, var(--deep-green) 50%, rgba(92,138,18,0) 100%);
    transform: rotate(-18deg);
  }
  .front-website {
    position: absolute;
    left: 54px; bottom: 22px;
    font-size: 15px;
    color: var(--white);
  }

  .card-back .brand-mark {
    left: 50%; top: 160px;
    transform: translateX(-50%);
  }
  .back-website {
    position: absolute;
    left: 0; right: 0; top: 226px;
    text-align: center;
    font-size: 15px;
    color: var(--white);
  }
</style>
</head>
<body>

  <section class="card card-front" aria-label="Business card front">
    <svg class="front-swoosh" viewBox="0 0 700 400" preserveAspectRatio="none" aria-hidden="true">
      <path d="M0,400 L0,318 C320,318 640,260 690,0 L700,0 L700,400 Z" fill="var(--peach)"/>
      <path d="M0,400 L0,338 C330,338 660,280 700,40 L700,400 Z" fill="var(--leaf-green)"/>
      <path d="M0,400 L0,372 C320,370 600,310 700,160 L700,400 Z" fill="var(--deep-green)" opacity="0.35"/>
      <path d="M120,322 C380,318 630,250 690,0" fill="none" stroke="var(--deep-green)" stroke-width="3"/>
    </svg>

    <div class="divider-line" aria-hidden="true"></div>

    <div class="brand-mark">
      <span class="brand-dot" aria-hidden="true"></span>
      <span class="brand-name">Bright Meadows</span>
    </div>

    <div class="contact-block">
      <p class="contact-name">Martin Reyes <span class="job-title">I Job Title</span></p>
      <p class="contact-address">Your address Goes Here, City,<br>Zip Code, Country Name</p>
      <p class="contact-line">
        <svg viewBox="0 0 16 16" aria-hidden="true"><path d="M4 1 L6.5 4.5 L5 6.5 C6 8.5 7.5 10 9.5 11 L11.5 9.5 L15 12 L13 15 C7 14 2 9 1 3 Z" fill="var(--accent-orange)"/></svg>
        322-5550-1473
      </p>
      <p class="contact-line">
        <svg viewBox="0 0 16 16" aria-hidden="true"><rect x="3" y="1" width="10" height="14" rx="2" fill="var(--accent-orange)"/><rect x="5" y="3" width="6" height="8" fill="var(--white)"/></svg>
        322-5550-1928
      </p>
      <p class="contact-line">
        <svg viewBox="0 0 16 16" aria-hidden="true"><rect x="1" y="3" width="14" height="10" rx="1" fill="var(--accent-orange)"/><path d="M1 4 L8 9 L15 4" fill="none" stroke="var(--white)" stroke-width="1.4"/></svg>
        info@brightmeadows.com
      </p>
    </div>

    <p class="front-website">www.brightmeadows.com</p>
  </section>

  <section class="card card-back" aria-label="Business card back">
    <div class="brand-mark">
      <span class="brand-dot" aria-hidden="true"></span>
      <span class="brand-name">Bright Meadows</span>
    </div>
    <p class="back-website">www.brightmeadows.com</p>
  </section>

</body>
</html>
```